Redesign of business card for Cedar Ridge Mechanical

We are looking for a new design for our business cards for Cedar Ridge Mechanical. We are a plumbing & HVAC construction company, operating on the West Coast of Canada and USA. Logo attached.
Industry/Entity Type
Construction - Plumbing & HVAC
Contact Information for Business Card
Name, address, phone numbers, email, website address
Look and feel
Each slider illustrates characteristics of the customer's brand and the style your logo design should communicate.

```html
<!DOCTYPE html>
<html lang="en">
<head>
<meta charset="UTF-8">
<title>Cedar Ridge Mechanical – Business Card</title>
<link href="https://fonts.googleapis.com/css2?family=Poppins:wght@300;400;600;700&display=swap" rel="stylesheet">
<style>
  :root {
    --stage: #1e1e1e;
    --card: #232324;
    --ink: #ffffff;
    --ink-soft: #e6e6e6;
    --pattern-a: #2a2a2c;
    --pattern-b: #1c1c1d;
  }
  * { margin: 0; padding: 0; box-sizing: border-box; }
  html, body {
    width: 1200px; height: 711px; overflow: hidden;
    background: var(--stage);
    font-family: "Poppins", sans-serif;
    color: var(--ink);
  }
  .stage {
    position: relative; width: 1200px; height: 711px;
    display: flex; align-items: center; justify-content: center; gap: 40px;
  }
  .card {
    position: relative; width: 540px; height: 309px;
    background: var(--card);
    border-radius: 4px;
    box-shadow: 0 14px 30px rgba(0,0,0,.55);
    overflow: hidden;
  }
  /* Back side */
  .card-back__pattern {
    position: absolute; inset: 0;
    background: radial-gradient(ellipse at 70% 20%, var(--pattern-a), var(--pattern-b));
  }
  .card-back__brand {
    position: absolute; left: 340px; top: 148px;
    display: flex; align-items: center; gap: 6px;
    font-size: 9px; font-weight: 600; letter-spacing: .5px; text-transform: uppercase;
  }
  .brand-square {
    width: 12px; height: 12px; border: 2px solid var(--ink); border-radius: 2px;
  }
  /* Front side */
  .card-front__brand {
    position: absolute; right: 34px; top: 42px;
    display: flex; align-items: center; gap: 12px;
    font-size: 19px; font-weight: 600; letter-spacing: .6px; text-transform: uppercase;
    line-height: 1.15;
  }
  .card-front__brand .brand-square { width: 42px; height: 42px; border-width: 4px; border-radius: 6px; }
  .person {
    position: absolute; left: 30px; right: 0; top: 120px;
  }
  .person__headline {
    display: flex; align-items: flex-end;
  }
  .person__name { font-size: 30px; line-height: 1; white-space: nowrap; }
  .person__first { font-weight: 700; }
  .person__last { font-weight: 300; }
  .person__rule {
    flex: 1; height: 2px; margin: 0 0 5px 12px;
    background: var(--ink);
  }
  .person__title { margin-top: 8px; font-size: 15px; font-weight: 300; }
  .contact {
    position: absolute; right: 22px; top: 168px;
    font-size: 13.5px; font-weight: 300; line-height: 1.45;
    text-align: right; color: var(--ink-soft);
  }
  .contact__address { margin-bottom: 8px; margin-right: 26px; }
  .contact__row { display: flex; justify-content: flex-end; align-items: center; gap: 10px; }
  .contact__icon { width: 14px; height: 14px; fill: none; stroke: var(--ink); stroke-width: 1.6; }
</style>
</head>
<body>
<main class="stage">
  <section class="card card-back" aria-label="Card back">
    <div class="card-back__pattern" role="img" aria-label="Repeating embossed monogram pattern in dark grey tones"></div>
    <div class="card-back__brand"><span class="brand-square"></span>Cedar Ridge Mechanical</div>
  </section>

  <section class="card card-front" aria-label="Card front">
    <div class="card-front__brand"><span class="brand-square"></span><span>Cedar Ridge<br>Mechanical</span></div>

    <div class="person">
      <div class="person__headline">
        <p class="person__name"><span class="person__first">Marta</span> <span class="person__last">Velinova</span></p>
        <span class="person__rule"></span>
      </div>
      <p class="person__title">Founder &amp; CEO</p>
    </div>

    <div class="contact">
      <p class="contact__address">1840 Harbor Ln. Suite 310<br>Tacoma, WA 98402</p>
      <p class="contact__row">(253) 555-0147
        <svg class="contact__icon" viewBox="0 0 16 16"><path d="M3 2l3 1 1 3-2 1a8 8 0 0 0 4 4l1-2 3 1 1 3-2 2C7 15 1 9 1 4z"/></svg>
      </p>
      <p class="contact__row">www.yourwebsite.com
        <svg class="contact__icon" viewBox="0 0 16 16"><circle cx="8" cy="8" r="6.5"/><ellipse cx="8" cy="8" rx="3" ry="6.5"/><path d="M1.5 8h13"/></svg>
      </p>
      <p class="contact__row">info@yourwebsite.com
        <svg class="contact__icon" viewBox="0 0 16 16"><rect x="1.5" y="3.5" width="13" height="9" rx="1"/><path d="M1.5 4l6.5 5 6.5-5"/></svg>
      </p>
    </div>
  </section>
</main>
</body>
</html>
```